Kestova Information Posters for Student signage

Secondary school looking for some posters to display throughout the school with fresh designs using school colours and fitting with general feel of the school's graphic image. The final designs should be welcoming but clearly outline the required instructions. Sample designs that have been created by the school are attached with the relevant information that is required to appear on the signs. School would like a more dynamic design than the basic signs attached.
We are looking for:
- Large pop-up banner style size for the 2 posters called
"Ready for class" and "Morning Routine".
- Printable poster for the "Kestova Outdoor" sign.

Please incorporate a design feature of "the Kestova 1,2,3" into the posters and also use the Kestova Leaner values of Integrity, Compassion, Curiosity and Drive to help illustrate the content.

An option for design is to incorporate our school's first nations artwork into the design and i have also provided various extracts of design pieces that the school often uses in it's marketing materials.

Target Market(s)

Secondary School Students

Industry/Entity Type

Education

Colors
00AB8E
00BBA5
67D7C9
C6EFE9
E9F9F6
FFF300
FFF600
FEFA6F
FFFEC7
FFFEE8
FFC000
F8CF3A
FAE287
FDF2CF
FEFAEE

Requirements
Must have
• My project must have eyecatching graphics

```html
<!DOCTYPE html>
<html lang="en">
<head>
<meta charset="utf-8">
<title>Kestova Student Signage</title>
<link rel="stylesheet" href="https://fonts.googleapis.com/css2?family=Poppins:wght@600;700;800;900&family=Libre+Baskerville:ital,wght@1,700&display=swap">
<style>
:root{
  --ink:#0e4a45;
  --teal:#00AB8E;
  --teal-bright:#00BBA5;
  --teal-soft:#67D7C9;
  --teal-pale:#C6EFE9;
  --yellow:#FFF300;
  --yellow-soft:#FEFA6F;
  --white:#ffffff;
  --bg:#ebe8e3;
}
*{box-sizing:border-box;margin:0;padding:0}
html,body{width:1200px;height:800px;overflow:hidden;background:var(--bg)}
body{position:relative;font-family:"Poppins",sans-serif;color:var(--ink)}
.piece{position:absolute;background:var(--white);overflow:hidden;box-shadow:0 2px 10px rgba(0,0,0,.12)}
.banner{width:310px;height:740px;top:30px}
.banner--ready{left:40px}
.banner--routine{left:380px}
.poster{left:760px;top:30px;width:400px;height:555px}
.abs{position:absolute}
.artwork{position:absolute;border-radius:0 0 0 100%;
  background:radial-gradient(circle at 85% 15%,var(--yellow-soft) 0%,var(--teal-pale) 45%,rgba(255,255,255,0) 75%)}
.brand{position:absolute;display:flex;align-items:center;gap:6px;font-weight:800;color:var(--ink)}
.brand-dot{width:14px;height:14px;border-radius:50%;background:var(--yellow);border:3px solid var(--ink)}
.h-dark{font-weight:900;color:var(--ink);line-height:1;letter-spacing:-1px;position:absolute;white-space:nowrap}
.h-teal{font-weight:900;color:var(--teal-bright);line-height:1;letter-spacing:-2px;position:absolute;white-space:nowrap}
.kest123{position:absolute;display:flex;align-items:center;background:var(--yellow);border-radius:4px;padding:3px}
.kest123-name{font-weight:700;color:var(--ink);padding:0 8px}
.kest123-nums{display:flex;gap:4px;background:var(--white);border-radius:3px;padding:4px 6px}
.num{display:flex;align-items:center;justify-content:center;border-radius:50%;color:var(--white);font-weight:700}
.num--teal{background:var(--teal-bright)}
.num--ink{background:var(--ink)}
.ready-item{position:absolute;left:0;width:310px;display:flex;align-items:center}
.ready-item .num{width:33px;height:33px;font-size:20px;margin-left:28px}
.icon-disc{display:flex;align-items:center;justify-content:center;border-radius:50%;background:var(--yellow)}
.ready-item .icon-disc{width:72px;height:72px;margin-left:10px}
.ready-text{margin-left:16px;font-weight:700;font-size:24px;line-height:.95;color:var(--ink)}
.ready-text small{display:block;font-size:12px;font-weight:600;margin-top:4px}
.dots{position:absolute;border-top:2px dotted var(--teal)}
.wave{position:absolute;left:0;bottom:0;width:100%}
.values{position:absolute;left:0;width:100%;text-align:center;color:var(--white);line-height:1.1}
.values-main{font-weight:700}
.values-sub{font-weight:600}
.tagline{position:absolute;left:0;width:100%;text-align:center;font-family:"Libre Baskerville",serif;font-style:italic;font-weight:700;font-size:14.5px;color:var(--ink)}
.step-box{position:absolute;left:18px;width:274px;border:2px solid var(--yellow);border-radius:4px}
.step-pill{position:absolute;left:50%;transform:translateX(-50%);background:var(--yellow);color:var(--ink);font-weight:800;font-size:15px;padding:1px 8px;border-radius:4px;white-space:nowrap;letter-spacing:-.3px}
.step-row{position:absolute;left:36px;display:flex;align-items:center;transform:translateY(-50%)}
.step-row .num{width:32px;height:32px;font-size:19px}
.step-row .icon-disc{width:33px;height:33px;margin-left:14px}
.step-text{margin-left:15px;font-weight:700;font-size:11.5px;line-height:1.15;color:var(--ink);width:150px}
.hats-box{position:absolute;left:25px;top:185px;width:353px;height:251px;border:3px solid var(--yellow);border-radius:5px}
.hats-row{position:absolute;left:44px;display:flex;align-items:center;transform:translateY(-50%)}
.hats-row .icon-disc{width:59px;height:59px}
.hats-word{margin-left:20px;font-weight:800;font-size:43px;color:var(--ink);letter-spacing:-.5px;line-height:1}
</style>
</head>
<body>

<!-- Banner: Ready for class -->
<section class="piece banner banner--ready">
  <div class="artwork" style="right:0;top:0;width:230px;height:200px" role="img" aria-label="First Nations style dot artwork radiating from the top corner in teal and yellow"></div>
  <div class="brand" style="right:22px;top:36px;font-size:16px"><span class="brand-dot"></span>Kestova</div>
  <h1 class="h-dark" style="left:18px;top:95px;font-size:40px">ARE YOU</h1>
  <div class="h-teal" style="left:14px;top:132px;font-size:80px">READY</div>
  <div class="h-dark" style="left:18px;top:208px;font-size:42px">FOR CLASS?</div>

  <div class="kest123" style="left:18px;top:275px;width:274px;height:42px">
    <span class="kest123-name" style="font-size:22px">The Kestova</span>
    <span class="kest123-nums"><span class="num num--teal" style="width:24px;height:24px;font-size:14px">1</span><span class="num num--teal" style="width:24px;height:24px;font-size:14px">2</span><span class="num num--teal" style="width:24px;height:24px;font-size:14px">3</span></span>
  </div>

  <div class="ready-item" style="top:339px">
    <span class="num num--teal">1</span>
    <span class="icon-disc"><svg width="40" height="30" viewBox="0 0 40 30"><rect x="6" y="2" width="28" height="19" rx="2" fill="var(--ink)"/><rect x="1" y="22" width="38" height="5" rx="2" fill="var(--ink)"/></svg></span>
    <span class="ready-text">Laptop /<br>workbook</span>
  </div>
  <div class="dots" style="left:18px;width:274px;top:433px"></div>

  <div class="ready-item" style="top:452px">
    <span class="num num--teal">2</span>
    <span class="icon-disc"><svg width="30" height="52" viewBox="0 0 30 52"><rect x="3" y="2" width="24" height="48" rx="6" fill="none" stroke="var(--ink)" stroke-width="3"/><circle cx="15" cy="11" r="3" fill="none" stroke="var(--ink)" stroke-width="2"/><rect x="7" y="30" width="16" height="14" rx="2" fill="var(--ink)"/></svg></span>
    <span class="ready-text">Phone in<br>Pouchlok</span>
  </div>
  <div class="dots" style="left:18px;width:274px;top:546px"></div>

  <div class="ready-item" style="top:567px">
    <span class="num num--teal">3</span>
    <span class="icon-disc"><svg width="54" height="30" viewBox="0 0 54 30"><path d="M16 6 Q27 0 38 6 L41 20 L13 20 Z" fill="var(--ink)"/><path d="M3 24 Q27 14 51 24 Q27 30 3 24 Z" fill="var(--ink)"/></svg></span>
    <span class="ready-text">Correct<br>uniform<small>(Including hat)</small></span>
  </div>

  <svg class="wave" height="92" viewBox="0 0 310 92" preserveAspectRatio="none">
    <path d="M0 22 C60 0 110 40 170 22 S270 -2 310 6 L310 92 L0 92Z" fill="var(--teal-soft)"/>
    <path d="M0 40 C60 18 110 56 170 38 S270 8 310 16 L310 92 L0 92Z" fill="var(--teal-bright)"/>
  </svg>
  <div class="values" style="top:694px"><div class="values-main" style="font-size:15px">Curiosity and Drive</div><div class="values-sub" style="font-size:11px">Kestova Learner Values</div></div>
</section>

<!-- Banner: Morning routine -->
<section class="piece banner banner--routine">
  <div class="artwork" style="right:0;top:0;width:230px;height:200px" role="img" aria-label="First Nations style dot artwork radiating from the top corner in teal and yellow"></div>
  <div class="brand" style="right:22px;top:34px;font-size:16px"><span class="brand-dot"></span>Kestova</div>
  <h1 class="h-dark" style="left:18px;top:78px;font-size:38px">MORNING</h1>
  <div class="h-teal" style="left:16px;top:112px;font-size:56px">ROUTINE</div>

  <div class="kest123" style="left:18px;top:170px;width:274px;height:44px">
    <span class="kest123-name" style="font-size:22px">The Kestova</span>
    <span class="kest123-nums"><span class="num num--ink" style="width:26px;height:26px;font-size:15px">1</span><span class="num num--ink" style="width:26px;height:26px;font-size:15px">2</span><span class="num num--ink" style="width:26px;height:26px;font-size:15px">3</span></span>
  </div>
  <p class="tagline" style="top:224px">Early is on time, on time is late!</p>

  <div class="step-box" style="top:266px;height:178px"></div>
  <div class="step-pill" style="top:256px">ON TIME</div>
  <div class="step-row" style="top:303px"><span class="num num--ink">1</span><span class="icon-disc"><svg width="22" height="22" viewBox="0 0 22 22"><circle cx="11" cy="11" r="9" fill="none" stroke="var(--ink)" stroke-width="2"/><path d="M11 5 V11 L15 14" stroke="var(--ink)" stroke-width="2" fill="none"/></svg></span><span class="step-text">Arrive before<br>8:30 AM</span></div>
  <div class="dots" style="left:36px;width:238px;top:331px"></div>
  <div class="step-row" style="top:359px"><span class="num num--ink">2</span><span class="icon-disc"><svg width="22" height="20" viewBox="0 0 22 20"><rect x="1" y="1" width="6" height="18" fill="var(--ink)"/><rect x="8" y="1" width="6" height="18" fill="var(--ink)"/><rect x="15" y="1" width="6" height="18" fill="var(--ink)"/></svg></span><span class="step-text">Place Bag in<br>Locker</span></div>
  <div class="dots" style="left:36px;width:238px;top:384px"></div>
  <div class="step-row" style="top:415px"><span class="num num--ink">3</span><span class="icon-disc" role="img" aria-label="Group assembly icon"></span><span class="step-text">Arrive at Home Group / House Assembly before 8:40 AM</span></div>

  <div class="step-box" style="top:470px;height:178px"></div>
  <div class="step-pill" style="top:459px">RUNNING LATE</div>
  <div class="step-row" style="top:507px"><span class="num num--ink">1</span><span class="icon-disc" role="img" aria-label="School office building icon"></span><span class="step-text">Sign in at<br>Student Services</span></div>
  <div class="dots" style="left:36px;width:238px;top:536px"></div>
  <div class="step-row" style="top:563px"><span class="num num--ink">2</span><span class="icon-disc"><svg width="22" height="20" viewBox="0 0 22 20"><rect x="1" y="1" width="6" height="18" fill="var(--ink)"/><rect x="8" y="1" width="6" height="18" fill="var(--ink)"/><rect x="15" y="1" width="6" height="18" fill="var(--ink)"/></svg></span><span class="step-text">Place bag in Locker</span></div>
  <div class="dots" style="left:36px;width:238px;top:589px"></div>
  <div class="step-row" style="top:619px"><span class="num num--ink">3</span><span class="icon-disc" role="img" aria-label="Class group icon"></span><span class="step-text">Prompt arrival to<br>class expected</span></div>

  <svg class="wave" height="86" viewBox="0 0 310 86" preserveAspectRatio="none">
    <path d="M0 18 C60 0 110 36 170 20 S270 -2 310 4 L310 86 L0 86Z" fill="var(--teal-soft)"/>
    <path d="M0 36 C60 16 110 50 170 34 S270 8 310 14 L310 86 L0 86Z" fill="var(--teal-bright)"/>
  </svg>
  <div class="values" style="top:700px"><div class="values-main" style="font-size:15px">Integrity</div><div class="values-sub" style="font-size:11px">Kestova Learner Values</div></div>
</section>

<!-- Poster: Hats outdoors -->
<section class="piece poster">
  <div class="artwork" style="right:0;top:0;width:260px;height:190px" role="img" aria-label="First Nations style dot artwork radiating from the top corner in teal and yellow"></div>
  <div class="brand" style="right:22px;top:52px;font-size:17px"><span class="brand-dot"></span>Kestova</div>
  <h1 class="h-dark" style="left:25px;top:27px;font-size:30px">WE WEAR</h1>
  <div class="h-teal" style="left:22px;top:56px;font-size:78px">HATS</div>
  <div class="h-dark" style="left:25px;top:135px;font-size:17.5px;letter-spacing:-.3px">AT KESTOVA WHEN OUTDOORS...</div>

  <div class="hats-box"></div>
  <div class="kest123" style="left:76px;top:167px;height:36px;border-radius:8px">
    <span class="kest123-name" style="font-size:19px">The Kestova</span>
    <span class="kest123-nums" style="border-radius:6px"><span class="num num--ink" style="width:21px;height:21px;font-size:12px">1</span><span class="num num--ink" style="width:21px;height:21px;font-size:12px">2</span><span class="num num--ink" style="width:21px;height:21px;font-size:12px">3</span></span>
  </div>

  <div class="hats-row" style="top:248px"><span class="icon-disc" role="img" aria-label="Student walking icon"></span><span class="hats-word">WALKING</span></div>
  <div class="dots" style="left:44px;width:318px;top:287px"></div>
  <div class="hats-row" style="top:323px"><span class="icon-disc" role="img" aria-label="Student sitting icon"></span><span class="hats-word">SITTING</span></div>
  <div class="dots" style="left:44px;width:318px;top:362px"></div>
  <div class="hats-row" style="top:398px"><span class="icon-disc" role="img" aria-label="Student playing with ball icon"></span><span class="hats-word">PLAYING</span></div>

  <svg class="wave" height="108" viewBox="0 0 400 108" preserveAspectRatio="none">
    <path d="M0 20 C80 0 140 48 220 26 S350 -4 400 6 L400 108 L0 108Z" fill="var(--teal-soft)"/>
    <path d="M0 42 C80 20 140 66 220 44 S350 12 400 20 L400 108 L0 108Z" fill="var(--teal-bright)"/>
  </svg>
  <div class="values" style="top:502px"><div class="values-main" style="font-size:19px">Integrity</div><div class="values-sub" style="font-size:13px">Kestova Learner Values</div></div>
</section>

</body>
</html>
```